Posters for showcases and a door for a driving school In front of a university

We need a design showcase with our logo for the right windows, the middle door and the left window. The design should cover 50-66% of the height of the showcase. We seek to reach a panel of young people, 18-25 years old It is a blue background (see appendix) The design can cover the 3 surfaces Window width 140 cm - door width 150 cm As an example in the attachments, an old publication on file 4. NEW 8.8.2018: A suggestion, a mix between file 4 and file 5 NEW 12.08.2018 FILE 7 ... That's what would make you win !!! Thanks We need a showcase with our logo for the right windows, the middle door and the left window. The design should cover 50-66% of the height of the showcase We seek to reach a panel of young people, 18-25 years old It must contain a white L on a blue background (see attached image)
Target Market(s)
Young people from 18 years
Colors
Designer to choose colors to be used in the design.
Requirements
Must have
- It is a blue background (see appendix)
Nice to have
- A road and / or signals, and / or a person, anything that may be related to the learning course
Should not have
- The design too simple. No need for a designer for an L on a blue background

```html
<!DOCTYPE html>
<html lang="fr">
<head>
<meta charset="utf-8">
<title>Cap Route Auto-École – Vitrines</title>
<link rel="stylesheet" href="https://fonts.googleapis.com/css2?family=Montserrat:wght@600&family=Open+Sans:wght@400&family=Yellowtail&display=swap">
<style>
  :root {
    --orange: #f07a1c;
    --orange-light: #f8b638;
    --gold: #f5a623;
    --blue: #1f6fc0;
    --blue-dark: #1a4f9c;
    --navy: #0c2348;
    --ink: #111a2b;
    --white: #ffffff;
    --globe: #1a9e8a;
  }
  html, body { margin: 0; padding: 0; overflow: hidden; }
  body { width: 1200px; height: 1200px; background: var(--white); position: relative; font-family: "Open Sans", sans-serif; }

  /* Poster (portrait panel) */
  .poster { position: absolute; left: 80px; top: 300px; width: 360px; height: 606px; overflow: hidden; }
  .poster svg { display: block; }
  .poster-slogan { position: absolute; right: 14px; top: 150px; text-align: right;
    font-family: "Yellowtail", cursive; color: var(--blue-dark); font-size: 44px; line-height: 72px;
    transform: scaleX(0.78); transform-origin: right top; }
  .poster-slogan span { display: block; white-space: nowrap; }
  .poster-brand { position: absolute; left: 16px; top: 520px; width: 84px; height: 40px; background: var(--white);
    font-family: "Montserrat", sans-serif; font-weight: 600; color: var(--orange); font-size: 10px;
    display: flex; align-items: center; justify-content: center; gap: 4px; white-space: nowrap; }
  .poster-brand .dot { width: 7px; height: 7px; border-radius: 50%; background: var(--orange); }
  .poster-phone { position: absolute; left: 128px; top: 516px; font-size: 24px; color: var(--ink); display: flex; align-items: center; gap: 6px; white-space: nowrap; }
  .poster-web { position: absolute; left: 128px; top: 556px; font-size: 12px; color: var(--ink); display: flex; align-items: center; gap: 6px; white-space: nowrap; }

  /* Banner (square panel) */
  .banner { position: absolute; left: 635px; top: 300px; width: 527px; height: 624px; overflow: hidden; }
  .brand { position: absolute; left: 0; top: 40px; width: 527px; display: flex; align-items: center; justify-content: center; gap: 14px; }
  .brand .dot { width: 32px; height: 32px; border-radius: 50%; background: var(--orange); }
  .brand-name { font-family: "Montserrat", sans-serif; font-weight: 600; color: var(--orange); font-size: 48px; letter-spacing: 9px; white-space: nowrap; }
  .brand-sub { position: absolute; left: 0; top: 118px; width: 527px; text-align: center; font-family: "Montserrat", sans-serif; font-weight: 600; color: var(--blue-dark); font-size: 15px; letter-spacing: 18px; }
  .slogan { position: absolute; left: 0; top: 146px; width: 527px; text-align: center; font-family: "Yellowtail", cursive; font-size: 42px; line-height: 60px; color: var(--gold); white-space: nowrap; }
  .visual { position: absolute; left: 0; top: 216px; width: 527px; height: 408px; }
  .phone { position: absolute; left: 205px; top: 534px; font-size: 40px; color: var(--ink); display: flex; align-items: center; gap: 10px; white-space: nowrap; }
  .web { position: absolute; left: 140px; top: 588px; font-size: 21px; color: var(--blue-dark); display: flex; align-items: center; gap: 12px; white-space: nowrap; }
</style>
</head>
<body>

<section class="poster">
  <svg width="360" height="606" viewBox="0 0 360 606">
    <defs>
      <linearGradient id="posterBg" x1="0" y1="0" x2="1" y2="1">
        <stop offset="0" stop-color="#f8b638"/>
        <stop offset="1" stop-color="#f07a1c"/>
      </linearGradient>
      <radialGradient id="wheelPhoto"><stop offset="0" stop-color="#c9ccd2"/><stop offset="1" stop-color="#4a4e57"/></radialGradient>
    </defs>
    <rect width="360" height="606" fill="url(#posterBg)"/>
    <path d="M0,60 C80,20 150,40 220,70 C290,100 330,80 360,50 L360,120 C300,150 240,120 180,100 C110,80 50,90 0,110 Z" fill="#1f6fc0"/>
    <path d="M0,430 C80,460 150,480 230,430 C290,395 330,400 360,410 L360,470 C300,480 250,500 180,500 C100,500 40,480 0,470 Z" fill="#1f6fc0"/>
    <path d="M0,470 C60,490 120,505 200,500 C280,495 330,470 360,460 L360,510 C300,530 230,525 180,520 C100,515 40,505 0,500 Z" fill="#ffffff"/>
    <polygon points="85,20 150,110 85,200 20,110" fill="#1f6fc0"/>
    <path d="M72,60 H88 V140 H112 V156 H72 Z" fill="#ffffff"/>
    <circle cx="100" cy="340" r="72" fill="url(#wheelPhoto)" role="img" aria-label="Photo : mains d'un élève sur un volant"/>
  </svg>
  <div class="poster-slogan"><span>Offrez-vous</span><span>plus de plus</span><span>de liberté</span></div>
  <div class="poster-brand"><span class="dot"></span>CAP ROUTE</div>
  <div class="poster-phone">
    <svg width="18" height="18" viewBox="0 0 24 24"><path d="M6.6 10.8a15 15 0 0 0 6.6 6.6l2.2-2.2a1 1 0 0 1 1-.25 11 11 0 0 0 3.6.6 1 1 0 0 1 1 1V20a1 1 0 0 1-1 1A17 17 0 0 1 3 4a1 1 0 0 1 1-1h3.5a1 1 0 0 1 1 1 11 11 0 0 0 .6 3.6 1 1 0 0 1-.25 1Z" fill="#1a4f9c"/></svg>
    0761234567
  </div>
  <div class="poster-web">
    <svg width="13" height="13" viewBox="0 0 24 24"><circle cx="12" cy="12" r="10" fill="none" stroke="#1a9e8a" stroke-width="2"/><path d="M2 12h20M12 2c3 3 3 17 0 20M12 2c-3 3-3 17 0 20" fill="none" stroke="#1a9e8a" stroke-width="2"/></svg>
    www.autoecole-caproute.ch
  </div>
</section>

<section class="banner">
  <div class="brand"><span class="dot"></span><span class="brand-name">CAP ROUTE</span></div>
  <div class="brand-sub">AUTO - ÉCOLE</div>
  <div class="slogan">Offrez-vous plus de liberté</div>

  <svg class="visual" width="527" height="408" viewBox="0 0 527 408">
    <defs>
      <linearGradient id="cabinPhoto" x1="0" y1="0" x2="1" y2="1">
        <stop offset="0" stop-color="#6b6470"/>
        <stop offset="0.5" stop-color="#2f3136"/>
        <stop offset="1" stop-color="#5b5e66"/>
      </linearGradient>
      <linearGradient id="greyBase" x1="0" y1="0" x2="0" y2="1">
        <stop offset="0" stop-color="#f6f6f6"/><stop offset="1" stop-color="#d8d8d8"/>
      </linearGradient>
    </defs>
    <rect width="527" height="408" fill="url(#cabinPhoto)" role="img" aria-label="Photo : mains sur le volant d'une voiture, vue de l'habitacle"/>
    <path d="M0,0 H120 C140,120 180,180 240,210 C300,240 380,240 460,220 L0,220 Z" fill="#0c2348"/>
    <path d="M70,200 C130,170 170,170 210,210 C280,280 420,290 500,240 L500,260 C420,320 260,310 180,270 C130,250 100,250 70,260 Z" fill="#f07a1c"/>
    <path d="M0,200 C50,210 100,240 150,270 C250,320 400,320 500,250 L527,230 L527,408 L0,408 Z" fill="url(#greyBase)"/>
    <path d="M0,200 C40,200 60,210 70,215 L70,260 C40,250 20,250 0,255 Z" fill="#222"/>
    <polygon points="86,232 165,312 86,392 7,312" fill="#1f6fc0"/>
    <path d="M70,262 H86 V340 H122 V356 H70 Z" fill="#ffffff"/>
  </svg>

  <div class="phone">
    <svg width="38" height="38" viewBox="0 0 24 24"><path d="M6.6 10.8a15 15 0 0 0 6.6 6.6l2.2-2.2a1 1 0 0 1 1-.25 11 11 0 0 0 3.6.6 1 1 0 0 1 1 1V20a1 1 0 0 1-1 1A17 17 0 0 1 3 4a1 1 0 0 1 1-1h3.5a1 1 0 0 1 1 1 11 11 0 0 0 .6 3.6 1 1 0 0 1-.25 1Z" fill="#1a4f9c"/></svg>
    0761234567
  </div>
  <div class="web">
    <svg width="32" height="32" viewBox="0 0 24 24"><circle cx="12" cy="12" r="10" fill="none" stroke="#1a9e8a" stroke-width="2"/><path d="M2 12h20M12 2c3 3 3 17 0 20M12 2c-3 3-3 17 0 20M4 7h16M4 17h16" fill="none" stroke="#1a9e8a" stroke-width="1.6"/></svg>
    www.autoecole-caproute.ch
  </div>
</section>

</body>
</html>
```